Fun A1 2012 family planner using clever typography and block colour

I have been looking for an A1 2012 family planner and I have not been able to find one. Hence I would like help to develop such a planner. I plan to print it on matt paper, portrait orientated. I have attached some reference pictures of our 2011 planner. I like interesting typography, clear clean colours and simple illustration. I need space to write in daily events and need the weeks and days to be clearly delineated from each other. Each day cell needs the date and day in it (please refer to the file uploaded for a visual reference confirming this). Each weekend needs some kind of colour/ typographic delineation. I want a design for a year-at-a-view calendar. I plan to print the planner in Sydney, Australia with brightloomprints.com.au and probably to sell printed copies online. The terms & conditions of this project are that I will own the design concept 100% and in perpetuity worldwide once payment has been made. (NB. The attached Work File in Word contains a rough layout and all months, days and dates all typed up to make for quicker design.)

Target Market(s)

Reasonably well heeled family of 4. 2 parents. 2 kids. 2 pets.

Industry/Entity Type

Events

Requirements
Must have
• The calendar must be portrait (not landscape orientated), A1 size. It will be printed on matt paper by brightloomprints.com.au. It must have months running left to right (Jan-Dec) and day/date cells running top to bottom (refer 2011 planner photos in file uploaded). The day/ date cells must be around 3(w)x2(h)cm - big enough to write daily events in. Weekends must be colour/ typographically delineated. 2012 year must be noted as must "A Pebblegate Inc Project" and web address in fine print bottom left hand left hand corner.
Nice to have
• A Pebblegate Inc logo in bottom left hand corder (perhaps Nimble Owl like: http://www.artmarketly.com/design_submission.aspx?designid=731462). Header/Footer space for customisation (e.g. "Hartono-Quist 2012 Planner" or "XYZ Co 2012 Planner".
Should not have
• The calendar should not use photographs or resemble standard or cheesy wall calendars. No watermarks please.

```html
<!DOCTYPE html>
<html lang="en">
<head>
<meta charset="utf-8">
<title>2012 Planner</title>
<link href="https://fonts.googleapis.com/css2?family=Arimo:wght@400;700&display=swap" rel="stylesheet">
<style>
:root{
  --jan:#86d1c3; --feb:#fbb04b; --mar:#a17bb4; --apr:#acd98d;
  --may:#f47b2f; --jun:#e21a5e; --jul:#17a99a; --aug:#d5e026;
  --sep:#e21d5d; --oct:#b19c4a; --nov:#9d1f63; --dec:#4a4a4a;
  --paper:#ffffff;
}
*{margin:0;padding:0;box-sizing:border-box}
html,body{width:848px;height:1200px;overflow:hidden;background:var(--paper)}
body{position:relative;font-family:"Arimo",Arial,sans-serif}
.year{position:absolute;left:2px;top:-9px;font-size:40px;font-weight:700;color:var(--jan);letter-spacing:1px;line-height:1}
.calendar{position:absolute;left:5px;top:30px;display:flex;gap:5.7px}
.month{width:62px;list-style:none;color:var(--c)}
.month h2{height:33px;background:var(--c);color:#fff;font-size:16px;font-weight:700;padding:1px 0 0 3px;margin-bottom:5px;line-height:18px}
.month li{position:relative;height:34.5px;padding:0 0 0 17px;font-size:6.3px;font-weight:700;text-transform:uppercase;line-height:9px;white-space:nowrap}
.month li b{position:absolute;left:0;top:0;width:14px;height:28px;border:1.4px solid var(--c);writing-mode:vertical-rl;transform:rotate(180deg);font-size:12.5px;line-height:11.5px;text-align:center;font-weight:700;color:var(--c);background:var(--paper)}
.month li.we b{background:var(--c);color:#fff}
.jan{--c:var(--jan)}.feb{--c:var(--feb)}.mar{--c:var(--mar)}.apr{--c:var(--apr)}
.may{--c:var(--may)}.jun{--c:var(--jun)}.jul{--c:var(--jul)}.aug{--c:var(--aug)}
.sep{--c:var(--sep)}.oct{--c:var(--oct)}.nov{--c:var(--nov)}.dec{--c:var(--dec)}
.brand{position:absolute;left:55px;top:1068px;width:66px;text-align:center}
.brand-dot{width:30px;height:30px;border-radius:50%;background:var(--feb);margin:0 auto 6px}
.brand-name{font-size:12px;font-weight:400;color:var(--jul);white-space:nowrap}
</style>
</head>
<body>
<div class="year">2012</div>

<div class="calendar">
<ul class="month jan"><h2>JAN</h2>
<li class="we"><b>01</b>Sunday</li><li><b>02</b>Monday</li><li><b>03</b>Tuesday</li><li><b>04</b>Wednesday</li><li><b>05</b>Thursday</li><li><b>06</b>Friday</li><li class="we"><b>07</b>Saturday</li>
<li class="we"><b>08</b>Sunday</li><li><b>09</b>Monday</li><li><b>10</b>Tuesday</li><li><b>11</b>Wednesday</li><li><b>12</b>Thursday</li><li><b>13</b>Friday</li><li class="we"><b>14</b>Saturday</li>
<li class="we"><b>15</b>Sunday</li><li><b>16</b>Monday</li><li><b>17</b>Tuesday</li><li><b>18</b>Wednesday</li><li><b>19</b>Thursday</li><li><b>20</b>Friday</li><li class="we"><b>21</b>Saturday</li>
<li class="we"><b>22</b>Sunday</li><li><b>23</b>Monday</li><li><b>24</b>Tuesday</li><li><b>25</b>Wednesday</li><li><b>26</b>Thursday</li><li><b>27</b>Friday</li><li class="we"><b>28</b>Saturday</li>
<li class="we"><b>29</b>Sunday</li><li><b>30</b>Monday</li><li><b>31</b>Tuesday</li>
</ul>
<ul class="month feb"><h2>FEB</h2>
<li><b>01</b>Wednesday</li><li><b>02</b>Thursday</li><li><b>03</b>Friday</li><li class="we"><b>04</b>Saturday</li><li class="we"><b>05</b>Sunday</li><li><b>06</b>Monday</li><li><b>07</b>Tuesday</li>
<li><b>08</b>Wednesday</li><li><b>09</b>Thursday</li><li><b>10</b>Friday</li><li class="we"><b>11</b>Saturday</li><li class="we"><b>12</b>Sunday</li><li><b>13</b>Monday</li><li><b>14</b>Tuesday</li>
<li><b>15</b>Wednesday</li><li><b>16</b>Thursday</li><li><b>17</b>Friday</li><li class="we"><b>18</b>Saturday</li><li class="we"><b>19</b>Sunday</li><li><b>20</b>Monday</li><li><b>21</b>Tuesday</li>
<li><b>22</b>Wednesday</li><li><b>23</b>Thursday</li><li><b>24</b>Friday</li><li class="we"><b>25</b>Saturday</li><li class="we"><b>26</b>Sunday</li><li><b>27</b>Monday</li><li><b>28</b>Tuesday</li>
<li><b>29</b>Wednesday</li>
</ul>
<ul class="month mar"><h2>MAR</h2>
<li><b>01</b>Thursday</li><li><b>02</b>Friday</li><li class="we"><b>03</b>Saturday</li><li class="we"><b>04</b>Sunday</li><li><b>05</b>Monday</li><li><b>06</b>Tuesday</li><li><b>07</b>Wednesday</li>
<li><b>08</b>Thursday</li><li><b>09</b>Friday</li><li class="we"><b>10</b>Saturday</li><li class="we"><b>11</b>Sunday</li><li><b>12</b>Monday</li><li><b>13</b>Tuesday</li><li><b>14</b>Wednesday</li>
<li><b>15</b>Thursday</li><li><b>16</b>Friday</li><li class="we"><b>17</b>Saturday</li><li class="we"><b>18</b>Sunday</li><li><b>19</b>Monday</li><li><b>20</b>Tuesday</li><li><b>21</b>Wednesday</li>
<li><b>22</b>Thursday</li><li><b>23</b>Friday</li><li class="we"><b>24</b>Saturday</li><li class="we"><b>25</b>Sunday</li><li><b>26</b>Monday</li><li><b>27</b>Tuesday</li><li><b>28</b>Wednesday</li>
<li><b>29</b>Thursday</li><li><b>30</b>Friday</li><li class="we"><b>31</b>Saturday</li>
</ul>
<ul class="month apr"><h2>APR</h2>
<li class="we"><b>01</b>Sunday</li><li><b>02</b>Monday</li><li><b>03</b>Tuesday</li><li><b>04</b>Wednesday</li><li><b>05</b>Thursday</li><li><b>06</b>Friday</li><li class="we"><b>07</b>Saturday</li>
<li class="we"><b>08</b>Sunday</li><li><b>09</b>Monday</li><li><b>10</b>Tuesday</li><li><b>11</b>Wednesday</li><li><b>12</b>Thursday</li><li><b>13</b>Friday</li><li class="we"><b>14</b>Saturday</li>
<li class="we"><b>15</b>Sunday</li><li><b>16</b>Monday</li><li><b>17</b>Tuesday</li><li><b>18</b>Wednesday</li><li><b>19</b>Thursday</li><li><b>20</b>Friday</li><li class="we"><b>21</b>Saturday</li>
<li class="we"><b>22</b>Sunday</li><li><b>23</b>Monday</li><li><b>24</b>Tuesday</li><li><b>25</b>Wednesday</li><li><b>26</b>Thursday</li><li><b>27</b>Friday</li><li class="we"><b>28</b>Saturday</li>
<li class="we"><b>29</b>Sunday</li><li><b>30</b>Monday</li>
</ul>
<ul class="month may"><h2>MAY</h2>
<li><b>01</b>Tuesday</li><li><b>02</b>Wednesday</li><li><b>03</b>Thursday</li><li><b>04</b>Friday</li><li class="we"><b>05</b>Saturday</li><li class="we"><b>06</b>Sunday</li><li><b>07</b>Monday</li>
<li><b>08</b>Tuesday</li><li><b>09</b>Wednesday</li><li><b>10</b>Thursday</li><li><b>11</b>Friday</li><li class="we"><b>12</b>Saturday</li><li class="we"><b>13</b>Sunday</li><li><b>14</b>Monday</li>
<li><b>15</b>Tuesday</li><li><b>16</b>Wednesday</li><li><b>17</b>Thursday</li><li><b>18</b>Friday</li><li class="we"><b>19</b>Saturday</li><li class="we"><b>20</b>Sunday</li><li><b>21</b>Monday</li>
<li><b>22</b>Tuesday</li><li><b>23</b>Wednesday</li><li><b>24</b>Thursday</li><li><b>25</b>Friday</li><li class="we"><b>26</b>Saturday</li><li class="we"><b>27</b>Sunday</li><li><b>28</b>Monday</li>
<li><b>29</b>Tuesday</li><li><b>30</b>Wednesday</li><li><b>31</b>Thursday</li>
</ul>
<ul class="month jun"><h2>JUN</h2>
<li><b>01</b>Friday</li><li class="we"><b>02</b>Saturday</li><li class="we"><b>03</b>Sunday</li><li><b>04</b>Monday</li><li><b>05</b>Tuesday</li><li><b>06</b>Wednesday</li><li><b>07</b>Thursday</li>
<li><b>08</b>Friday</li><li class="we"><b>09</b>Saturday</li><li class="we"><b>10</b>Sunday</li><li><b>11</b>Monday</li><li><b>12</b>Tuesday</li><li><b>13</b>Wednesday</li><li><b>14</b>Thursday</li>
<li><b>15</b>Friday</li><li class="we"><b>16</b>Saturday</li><li class="we"><b>17</b>Sunday</li><li><b>18</b>Monday</li><li><b>19</b>Tuesday</li><li><b>20</b>Wednesday</li><li><b>21</b>Thursday</li>
<li><b>22</b>Friday</li><li class="we"><b>23</b>Saturday</li><li class="we"><b>24</b>Sunday</li><li><b>25</b>Monday</li><li><b>26</b>Tuesday</li><li><b>27</b>Wednesday</li><li><b>28</b>Thursday</li>
<li><b>29</b>Friday</li><li class="we"><b>30</b>Saturday</li>
</ul>
<ul class="month jul"><h2>JUL</h2>
<li class="we"><b>01</b>Sunday</li><li><b>02</b>Monday</li><li><b>03</b>Tuesday</li><li><b>04</b>Wednesday</li><li><b>05</b>Thursday</li><li><b>06</b>Friday</li><li class="we"><b>07</b>Saturday</li>
<li class="we"><b>08</b>Sunday</li><li><b>09</b>Monday</li><li><b>10</b>Tuesday</li><li><b>11</b>Wednesday</li><li><b>12</b>Thursday</li><li><b>13</b>Friday</li><li class="we"><b>14</b>Saturday</li>
<li class="we"><b>15</b>Sunday</li><li><b>16</b>Monday</li><li><b>17</b>Tuesday</li><li><b>18</b>Wednesday</li><li><b>19</b>Thursday</li><li><b>20</b>Friday</li><li class="we"><b>21</b>Saturday</li>
<li class="we"><b>22</b>Sunday</li><li><b>23</b>Monday</li><li><b>24</b>Tuesday</li><li><b>25</b>Wednesday</li><li><b>26</b>Thursday</li><li><b>27</b>Friday</li><li class="we"><b>28</b>Saturday</li>
<li class="we"><b>29</b>Sunday</li><li><b>30</b>Monday</li><li><b>31</b>Tuesday</li>
</ul>
<ul class="month aug"><h2>AUG</h2>
<li><b>01</b>Wednesday</li><li><b>02</b>Thursday</li><li><b>03</b>Friday</li><li class="we"><b>04</b>Saturday</li><li class="we"><b>05</b>Sunday</li><li><b>06</b>Monday</li><li><b>07</b>Tuesday</li>
<li><b>08</b>Wednesday</li><li><b>09</b>Thursday</li><li><b>10</b>Friday</li><li class="we"><b>11</b>Saturday</li><li class="we"><b>12</b>Sunday</li><li><b>13</b>Monday</li><li><b>14</b>Tuesday</li>
<li><b>15</b>Wednesday</li><li><b>16</b>Thursday</li><li><b>17</b>Friday</li><li class="we"><b>18</b>Saturday</li><li class="we"><b>19</b>Sunday</li><li><b>20</b>Monday</li><li><b>21</b>Tuesday</li>
<li><b>22</b>Wednesday</li><li><b>23</b>Thursday</li><li><b>24</b>Friday</li><li class="we"><b>25</b>Saturday</li><li class="we"><b>26</b>Sunday</li><li><b>27</b>Monday</li><li><b>28</b>Tuesday</li>
<li><b>29</b>Wednesday</li><li><b>30</b>Thursday</li><li><b>31</b>Friday</li>
</ul>
<ul class="month sep"><h2>SEP</h2>
<li class="we"><b>01</b>Saturday</li><li class="we"><b>02</b>Sunday</li><li><b>03</b>Monday</li><li><b>04</b>Tuesday</li><li><b>05</b>Wednesday</li><li><b>06</b>Thursday</li><li><b>07</b>Friday</li>
<li class="we"><b>08</b>Saturday</li><li class="we"><b>09</b>Sunday</li><li><b>10</b>Monday</li><li><b>11</b>Tuesday</li><li><b>12</b>Wednesday</li><li><b>13</b>Thursday</li><li><b>14</b>Friday</li>
<li class="we"><b>15</b>Saturday</li><li class="we"><b>16</b>Sunday</li><li><b>17</b>Monday</li><li><b>18</b>Tuesday</li><li><b>19</b>Wednesday</li><li><b>20</b>Thursday</li><li><b>21</b>Friday</li>
<li class="we"><b>22</b>Saturday</li><li class="we"><b>23</b>Sunday</li><li><b>24</b>Monday</li><li><b>25</b>Tuesday</li><li><b>26</b>Wednesday</li><li><b>27</b>Thursday</li><li><b>28</b>Friday</li>
<li class="we"><b>29</b>Saturday</li><li class="we"><b>30</b>Sunday</li>
</ul>
<ul class="month oct"><h2>OCT</h2>
<li><b>01</b>Monday</li><li><b>02</b>Tuesday</li><li><b>03</b>Wednesday</li><li><b>04</b>Thursday</li><li><b>05</b>Friday</li><li class="we"><b>06</b>Saturday</li><li class="we"><b>07</b>Sunday</li>
<li><b>08</b>Monday</li><li><b>09</b>Tuesday</li><li><b>10</b>Wednesday</li><li><b>11</b>Thursday</li><li><b>12</b>Friday</li><li class="we"><b>13</b>Saturday</li><li class="we"><b>14</b>Sunday</li>
<li><b>15</b>Monday</li><li><b>16</b>Tuesday</li><li><b>17</b>Wednesday</li><li><b>18</b>Thursday</li><li><b>19</b>Friday</li><li class="we"><b>20</b>Saturday</li><li class="we"><b>21</b>Sunday</li>
<li><b>22</b>Monday</li><li><b>23</b>Tuesday</li><li><b>24</b>Wednesday</li><li><b>25</b>Thursday</li><li><b>26</b>Friday</li><li class="we"><b>27</b>Saturday</li><li class="we"><b>28</b>Sunday</li>
<li><b>29</b>Monday</li><li><b>30</b>Tuesday</li><li><b>31</b>Wednesday</li>
</ul>
<ul class="month nov"><h2>NOV</h2>
<li><b>01</b>Thursday</li><li><b>02</b>Friday</li><li class="we"><b>03</b>Saturday</li><li class="we"><b>04</b>Sunday</li><li><b>05</b>Monday</li><li><b>06</b>Tuesday</li><li><b>07</b>Wednesday</li>
<li><b>08</b>Thursday</li><li><b>09</b>Friday</li><li class="we"><b>10</b>Saturday</li><li class="we"><b>11</b>Sunday</li><li><b>12</b>Monday</li><li><b>13</b>Tuesday</li><li><b>14</b>Wednesday</li>
<li><b>15</b>Thursday</li><li><b>16</b>Friday</li><li class="we"><b>17</b>Saturday</li><li class="we"><b>18</b>Sunday</li><li><b>19</b>Monday</li><li><b>20</b>Tuesday</li><li><b>21</b>Wednesday</li>
<li><b>22</b>Thursday</li><li><b>23</b>Friday</li><li class="we"><b>24</b>Saturday</li><li class="we"><b>25</b>Sunday</li><li><b>26</b>Monday</li><li><b>27</b>Tuesday</li><li><b>28</b>Wednesday</li>
<li><b>29</b>Thursday</li><li><b>30</b>Friday</li>
</ul>
<ul class="month dec"><h2>DEC</h2>
<li class="we"><b>01</b>Saturday</li><li class="we"><b>02</b>Sunday</li><li><b>03</b>Monday</li><li><b>04</b>Tuesday</li><li><b>05</b>Wednesday</li><li><b>06</b>Thursday</li><li><b>07</b>Friday</li>
<li class="we"><b>08</b>Saturday</li><li class="we"><b>09</b>Sunday</li><li><b>10</b>Monday</li><li><b>11</b>Tuesday</li><li><b>12</b>Wednesday</li><li><b>13</b>Thursday</li><li><b>14</b>Friday</li>
<li class="we"><b>15</b>Saturday</li><li class="we"><b>16</b>Sunday</li><li><b>17</b>Monday</li><li><b>18</b>Tuesday</li><li><b>19</b>Wednesday</li><li><b>20</b>Thursday</li><li><b>21</b>Friday</li>
<li class="we"><b>22</b>Saturday</li><li class="we"><b>23</b>Sunday</li><li><b>24</b>Monday</li><li><b>25</b>Tuesday</li><li><b>26</b>Wednesday</li><li><b>27</b>Thursday</li><li><b>28</b>Friday</li>
<li class="we"><b>29</b>Saturday</li><li class="we"><b>30</b>Sunday</li><li><b>31</b>Monday</li>
</ul>
</div>

<div class="brand">
  <div class="brand-dot"></div>
  <div class="brand-name">Nimble Owl</div>
</div>
</body>
</html>
```